Business Card for a Life Coaching Company

MOSSVALE is a Life Coaching company that was initiated to support people who want to transform thier life or ana aspect of it.
our slogan is : "Dream. Believe. Succeed"
our logo is uploaded.
The name of the company implies that leadership, strength and wisdom required to change your life.
We want an attractive business card that would give an impression of reliability, support and change. so we really want it unique. Here are some examples of unique cards:

http://www.pixelharbornotes.example/2009/05/100-really-creative-business-cards/

MossVale is a life coaching organization focusing on individual transformation through the application of relevant and timeless principles of success.  MossVale believes that real, sustainable life transformations are brought about by tuning into the timeless wisdom we each carry in our hearts while boldy acting in the direction of our dreams.

Contacts on the card:
Address: 7 Tarek Ibn Nabil Heliopolis Cairo Egypt
Tel: +202 24 81 37 52
Fax: +202 24 81 37 19
Mobile: +2 012 574 9026 (Nadia Sherif)
+2 0199915815 (Kamal Rashidi)

By the way, our temporary website is http://www.mossvale.example

We have attached an .eps file with various configurations of our logo.

```html
<!DOCTYPE html>
<html lang="en">
<head>
<meta charset="utf-8">
<title>MossVale Business Card</title>
<link rel="stylesheet" href="https://fonts.googleapis.com/css2?family=Cinzel:wght@400;500&family=Tinos&display=swap">
<style>
  :root {
    --page: #eeeeee;
    --card: #573d2e;
    --orange: #ea8f4c;
    --orange-deep: #c9652e;
    --gold: #e6c98f;
    --cream: #eedbb4;
    --label: #e88752;
    --shade: #3f2a1f;
  }
  html, body {
    margin: 0;
    width: 1200px;
    height: 942px;
    overflow: hidden;
    background: var(--page);
  }
  .canvas {
    position: relative;
    width: 1200px;
    height: 942px;
  }
  .card {
    position: absolute;
    top: 240px;
    width: 562px;
    height: 336px;
    background: var(--card);
    overflow: hidden;
  }
  .card--back { left: 30px; }
  .card--front { left: 600px; }

  .illustration {
    position: absolute;
    top: 0;
    right: 0;
    height: 100%;
  }
  .card--back .illustration {
    width: 142px;
    background: linear-gradient(100deg, rgba(63,42,31,0) 0%, rgba(63,42,31,0.55) 45%, rgba(63,42,31,0.8) 100%);
  }
  .card--front .illustration {
    width: 184px;
    background: linear-gradient(110deg, rgba(234,143,76,0) 0%, rgba(234,143,76,0.75) 35%, var(--orange-deep) 100%);
  }

  .website {
    position: absolute;
    left: 48px;
    top: 152px;
    margin: 0;
    font-family: "Cinzel", serif;
    font-size: 20px;
    letter-spacing: 3.5px;
    color: var(--orange);
  }
  .contact {
    position: absolute;
    left: 50px;
    top: 202px;
    margin: 0;
    font-family: "Tinos", serif;
    font-size: 15px;
    line-height: 17.5px;
    color: var(--cream);
  }
  .contact .label { color: var(--label); }
  .contact div { white-space: nowrap; }

  .slogan {
    position: absolute;
    left: 46px;
    top: 44px;
    margin: 0;
    font-family: "Cinzel", serif;
    font-weight: 400;
    font-size: 64px;
    line-height: 62px;
    color: var(--orange);
  }
  .slogan span { display: block; }
  .brand-name {
    position: absolute;
    left: 48px;
    top: 230px;
    width: 322px;
    margin: 0;
    font-family: "Cinzel", serif;
    font-size: 19px;
    letter-spacing: 24px;
    color: var(--gold);
    white-space: nowrap;
  }
</style>
</head>
<body>
<main class="canvas">
  <section class="card card--back">
    <div class="illustration" role="img" aria-label="Faint lion head illustration in profile"></div>
    <p class="website">WWW.MOSSVALE.COM</p>
    <address class="contact" style="font-style:normal">
      <div><span class="label">Address:</span> 7 Tarek Ibn Nabil Heliopolis Cairo Egypt</div>
      <div><span class="label">Tel:</span> +202 24 81 37 52</div>
      <div><span class="label">Fax:</span> +202 24 81 37 19</div>
      <div><span class="label">Mobile:</span> +2 012 574 9026 (Nadia Sherif)</div>
      <div>+2 0196632470 (Kamal Rashidi)</div>
    </address>
  </section>

  <section class="card card--front">
    <h1 class="slogan"><span>BELIEVE</span><span>DREAM</span><span>SUCCEED</span></h1>
    <p class="brand-name">MOSSVALE</p>
    <div class="illustration" role="img" aria-label="Orange lion head illustration in profile"></div>
  </section>
</main>
</body>
</html>
```